2 sided Rack Card for Hotel Packages

Rack card advertising hotel packages - will need need to be front and back 3.5 x 8.5 - then will also need to be able to converted to an elevator poster 11x17. I have attached pictures but they are for examples or use they do NOT have to be used. Side 1 Headline: Plan your return Stay today!All packages include a Discount Special Rates*Spring Break Package (see attached image SpringBreakWaterparkM10) * All the following wording does not have to be used Package includes:Two Resort beach towelsTwo youth swim gogglesA $15 Parlotti's gift cardSpring Break Waterpark tote*Lunchbox Special Bramble Ridge Perks lunch bagPlastic lunch containerWater bottle* Fun in the Sun (see attached image FunInSun)Package includes:Two Resort beach towelsTwo youth swim gogglesTwo Resort sun visorsSunscreenFun in the Sun ToteToll Free Number: 800-317-5826 Website: www.resortatgovernorscrossing.comSide 2 - What's New for 2019*Sevierville ad is attached* Tidal Hollow Logo is attached *Heron Basin logo is attached Phone number: 800.317.5826 website: www.resortatgovernorscrossing.comAlso attached is the Resort Logo and artist rendition of Tidal Hollow

Target Market(s)

Guest that pick up Rack card in lobby

Industry/Entity Type

Hospitality

Requirements
Must have
• logo
• toll free
• website

```html
<!DOCTYPE html>
<html lang="en">
<head>
<meta charset="utf-8">
<title>Rack Card – Hotel Packages</title>
<link rel="stylesheet" href="https://fonts.googleapis.com/css2?family=Cinzel:wght@400;700&family=Oswald:wght@500;700&family=Raleway:ital,wght@0,400;0,500;0,600;1,600&display=swap">
<style>
  :root {
    --backdrop: #727272;
    --paper: #ffffff;
    --paper-shade: #d9d9d9;
    --teal: #5a7e86;
    --tan: #d4a06a;
    --brown: #7a5a3c;
    --body-brown: #5c4a3c;
    --ink: #222222;
    --sky: #1fa6e0;
  }
  * { margin: 0; padding: 0; box-sizing: border-box; }
  html, body { width: 988px; height: 1200px; overflow: hidden; }
  body { background: var(--backdrop); position: relative; font-family: "Raleway", sans-serif; }

  .rack-card {
    position: absolute; top: 180px; width: 329px; height: 800px;
    background: var(--paper); overflow: hidden;
  }
  .rack-card--front { left: 139px; }
  .rack-card--back { left: 536px; }

  /* Front */
  .brand-mark {
    position: absolute; top: 52px; left: 0; width: 100%;
    display: flex; flex-direction: column; align-items: center; gap: 6px;
    color: var(--brown); font-family: "Cinzel", serif; font-weight: 700; text-align: center;
  }
  .brand-mark__dot { width: 14px; height: 14px; border-radius: 50%; background: var(--tan); }
  .brand-mark__name { font-size: 25px; line-height: 1.1; }
  .front-photo {
    position: absolute; top: 126px; left: 0; width: 100%; height: 327px;
    background: linear-gradient(180deg, #a9a9ad 0%, #b9b6b6 40%, #8b94a3 100%);
  }
  .front-body {
    position: absolute; top: 453px; left: 0; width: 100%; height: 236px;
    background: linear-gradient(180deg, var(--paper) 0%, #ececec 100%);
  }
  .headline {
    margin-top: 36px; text-align: center; font-family: "Cinzel", serif; font-weight: 400;
    color: var(--brown); font-size: 28px; line-height: 25px; letter-spacing: 0.3px;
  }
  .headline__sub { font-size: 11.5px; font-family: "Raleway", sans-serif; font-weight: 600;
    font-style: italic; color: var(--ink); margin-top: 8px; text-align: center; }
  .partner-row {
    position: absolute; top: 150px; left: 0; width: 100%;
    display: flex; justify-content: space-around; align-items: center;
    font-family: "Raleway", sans-serif; font-weight: 600; font-size: 19px; color: var(--sky);
  }

  /* Back */
  .back-photo {
    position: absolute; top: 0; left: 0; width: 100%; height: 128px;
    background: linear-gradient(135deg, #2b4f9e 0%, #3c6fbf 50%, #c9c9cf 100%);
  }
  .back-body {
    position: absolute; top: 128px; left: 0; width: 100%; height: 562px;
    background: linear-gradient(180deg, #f6f6f6 0%, var(--paper-shade) 100%);
    padding: 32px 0 0 34px;
  }
  .package { margin-bottom: 20px; }
  .package__title { font-weight: 600; color: var(--tan); font-size: 19px; letter-spacing: 0.2px; margin-bottom: 10px; }
  .package__items { list-style: none; color: var(--body-brown); font-size: 15.5px; line-height: 19.5px; }
  .whats-new {
    margin-top: 10px; color: var(--brown); font-style: italic; font-weight: 600;
    font-size: 21.5px; line-height: 26px;
  }

  /* Shared contact band */
  .contact-band {
    position: absolute; left: 0; bottom: 0; width: 100%; height: 111px;
    background: var(--teal); color: var(--paper); text-align: center; font-family: "Oswald", sans-serif;
  }
  .contact-band__phone { font-weight: 700; font-size: 52px; line-height: 52px; margin-top: 15px; letter-spacing: -0.5px; }
  .contact-band__web { font-weight: 500; font-size: 14.5px; margin-top: 3px; letter-spacing: 0.2px; }
</style>
</head>
<body>
  <section class="rack-card rack-card--front">
    <div class="front-photo" role="img" aria-label="Three girls in swimsuits at the indoor water park"></div>
    <div class="brand-mark">
      <span class="brand-mark__dot"></span>
      <span class="brand-mark__name">The Lodge at<br>Willow Bend Point</span>
    </div>
    <div class="front-body">
      <h1 class="headline">Plan your return<br>Stay today!</h1>
      <p class="headline__sub">All packages include a Discount Special Rates*</p>
      <div class="partner-row">
        <span>Tidal Hollow</span>
        <span>Heron Basin</span>
      </div>
    </div>
    <div class="contact-band">
      <div class="contact-band__phone">800-317-5826</div>
      <div class="contact-band__web">WWW.LODGEATWILLOWBENDPOINT.EXAMPLE</div>
    </div>
  </section>

  <section class="rack-card rack-card--back">
    <div class="back-photo" role="img" aria-label="Girl splashing out of a water slide tube"></div>
    <div class="back-body">
      <div class="package">
        <h2 class="package__title">SPRING BREAK PACKAGE</h2>
        <ul class="package__items">
          <li>Two Resort beach towels</li>
          <li>Two youth swim goggles</li>
          <li>A $15 Parlotti's gift card</li>
          <li>Splashline Lagoon tote</li>
        </ul>
      </div>
      <div class="package">
        <h2 class="package__title">LUNCHBOX SPECIAL</h2>
        <ul class="package__items">
          <li>Bramble Ridge Perks lunch bag</li>
          <li>Plastic lunch container Water bottle*</li>
        </ul>
      </div>
      <div class="package">
        <h2 class="package__title">FUN IN THE SUN</h2>
        <ul class="package__items">
          <li>Two Resort beach towels</li>
          <li>Two youth swim goggles</li>
          <li>Two Resort sun visors</li>
          <li>Sunscreen</li>
        </ul>
      </div>
      <p class="whats-new">67 more Fully<br>Furnished Condos!<br>Heron Basin:<br>Featuring Firepits,<br>Hammock Area &amp;<br>Picnic Grounds</p>
    </div>
    <div class="contact-band">
      <div class="contact-band__phone">800-317-5826</div>
      <div class="contact-band__web">WWW.LODGEATWILLOWBENDPOINT.EXAMPLE</div>
    </div>
  </section>
</body>
</html>
```